Business card for law firm

Need business card for new law firm. Think confident, authoritative, conservative, but not stuffy or old-fashioned.

Contact Information for Business Card

Content for card - logo (uploaded), plus the following:

Paul Whitcombe (larger font)
Managing Partner (larger font, but not as large as name)
Level 9, 7 Ferris Lane
Sydney NSW 2000
Main Tel 02 9364 2710
Direct Tel 02 8472 3159
Email paul@qvlegal.com.au
www.qvlegal.com.au

Letterhead design should include logo plus:
Level 9, 7 Ferris Lane
Sydney NSW 2000
Tel 02 8472 3159
www.qvlegal.com.au

```html
<!DOCTYPE html>
<html lang="en">
<head>
<meta charset="utf-8">
<title>Quayvale Legal – Business Card</title>
<link rel="stylesheet" href="https://fonts.googleapis.com/css2?family=Cinzel:wght@400;500&family=Open+Sans:wght@400&display=swap">
<style>
  :root {
    --navy: #0b1d5a;
    --navy-deep: #0a1a52;
    --ink: #1c1c1c;
    --paper: #ffffff;
    --stage: #d9d9db;
    --rule: #c9ccd6;
  }
  * { margin: 0; padding: 0; box-sizing: border-box; }
  html, body { width: 1200px; height: 802px; overflow: hidden; }
  body { background: var(--stage); position: relative; font-family: "Open Sans", Arial, sans-serif; }

  .card { position: absolute; top: 274px; width: 443px; height: 265px; box-shadow: 0 3px 8px rgba(0,0,0,.25); }
  .card--front { left: 136px; background: var(--paper); }
  .card--back { left: 624px; background: var(--navy-deep); }

  .brand { position: absolute; left: 28px; top: 76px; width: 200px; text-align: center; color: var(--navy); }
  .brand__mark { display: block; width: 30px; height: 30px; margin: 0 auto 14px; background: var(--navy); }
  .brand__name { font-family: "Cinzel", Georgia, serif; font-size: 27px; line-height: 1; color: var(--ink); letter-spacing: 0.5px; }
  .brand__tag { font-family: "Cinzel", Georgia, serif; font-size: 10px; letter-spacing: 10px; margin-top: 6px; padding-left: 10px; color: var(--ink); }

  .divider { position: absolute; left: 231px; top: 67px; width: 1px; height: 130px; background: var(--rule); }

  .details { position: absolute; left: 246px; top: 63px; color: var(--ink); }
  .details__name { font-family: "Cinzel", Georgia, serif; font-size: 18px; font-weight: 500; color: var(--navy); line-height: 1.1; letter-spacing: 0.2px; }
  .details__role { font-size: 13px; line-height: 1.2; margin-bottom: 6px; }
  .contact { list-style: none; font-size: 12.5px; line-height: 16px; }
  .contact li { display: flex; align-items: center; }
  .contact svg { width: 9px; height: 9px; margin-right: 4px; fill: var(--navy); flex: none; }
  .contact small { font-size: 10.5px; margin-left: 3px; }
  .address { font-size: 12.5px; line-height: 16px; margin-top: 4px; }

  .back-name { position: absolute; right: 44px; top: 152px; font-family: "Cinzel", Georgia, serif; font-size: 17px; color: var(--paper); letter-spacing: 1px; }
</style>
</head>
<body>
  <section class="card card--front">
    <div class="brand">
      <span class="brand__mark"></span>
      <div class="brand__name">QUAYVALE</div>
      <div class="brand__tag">LEGAL</div>
    </div>
    <div class="divider"></div>
    <div class="details">
      <div class="details__name">PAUL WHITCOMBE</div>
      <div class="details__role">Managing Partner</div>
      <ul class="contact">
        <li><svg viewBox="0 0 10 10"><path d="M1 3.5C1 2 2.5 1 5 1s4 1 4 2.5V4.5H7V3.6H3v.9H1z M2.2 5h5.6L9 9H1z"/></svg>02 9364 2710</li>
        <li><svg viewBox="0 0 10 10"><path d="M1 3.5C1 2 2.5 1 5 1s4 1 4 2.5V4.5H7V3.6H3v.9H1z M2.2 5h5.6L9 9H1z"/></svg>02 8472 3159<small>(DIRECT)</small></li>
        <li><svg viewBox="0 0 10 10"><path d="M1 2h8v.8L5 5.5 1 2.8z M1 3.9l4 2.7 4-2.7V8H1z"/></svg>paul@qvlegal.com.au</li>
        <li><svg viewBox="0 0 10 10"><circle cx="5" cy="5" r="4.3"/></svg>www.qvlegal.com.au</li>
      </ul>
      <div class="address">Level 9, 7 Ferris Lane<br>Sydney NSW 2000</div>
    </div>
  </section>

  <section class="card card--back">
    <div class="back-name">QUAYVALE</div>
  </section>
</body>
</html>
```